Dietitian needs awesome business card

I need a contemporary design that's eye catching but professional.
My card is to given to doctors, specialists and patients alike.
I manage patients with chronic diseases
I have uploaded my logo and current business card, I would also like the other Certified Clinical Nutritionist logo incorporated into the design

Target Market(s)

Doctors, specialists and patients

Industry/Entity Type

Healthcare

Contact Information for Business Card

www.brightfieldnutrition.com.au
Ph: 0427 561 903
Fax: 6457 2183
email: marcus.k.diet@fernmail.com
Space on the back of the card with: Appointment date, Appointment time and appointment location

Font styles to use
Serif

Colors
fbee3e
876aae
ffc214

Requirements
Must have
• My Logo
• Certified Clinical Nutritionist Logo
• My 4 locations - Pinebrook Medical Centre, North Corrin Health, Hollis Medical, Ashcombe Doctors Surgery
Nice to have
• I like the colours in my current business card

```html
<!DOCTYPE html>
<html lang="en">
<head>
<meta charset="utf-8">
<title>Brightfield Nutrition &amp; Dietetics – Business Card</title>
<link rel="stylesheet" href="https://fonts.googleapis.com/css2?family=Marcellus&family=PT+Sans:wght@400;700&display=swap">
<style>
  :root {
    --bg: #e9e9ec;
    --card: #ffffff;
    --navy: #2e3a8c;
    --blue: #3c57a8;
    --green: #8cc63f;
    --orange: #f47b20;
    --ink: #3d3d4a;
    --rule: #b9bccb;
    --label-red: #c0392b;
  }
  * { margin: 0; padding: 0; box-sizing: border-box; }
  html, body { width: 1200px; height: 843px; overflow: hidden; }
  body {
    background: var(--bg);
    font-family: "PT Sans", Arial, sans-serif;
    color: var(--ink);
    display: flex;
    align-items: center;
    justify-content: center;
    gap: 40px;
  }
  .card {
    position: relative;
    width: 540px;
    height: 330px;
    background: var(--card);
    box-shadow: 0 2px 10px rgba(0,0,0,.12);
    overflow: hidden;
  }

  /* back side */
  .brand-small {
    position: absolute; left: 36px; top: 40px;
    display: flex; align-items: center; gap: 10px;
  }
  .brand-small .dot {
    width: 30px; height: 30px; border-radius: 50%; background: var(--blue);
  }
  .brand-small .name {
    font-family: "Marcellus", Georgia, serif;
    font-size: 24px; color: var(--navy); line-height: 1;
  }
  .brand-small .name small {
    display: block; font-size: 12px; color: var(--navy); margin-top: 3px;
  }
  .cert-badge {
    position: absolute; right: 36px; top: 22px;
    width: 104px; height: 44px; border-radius: 3px;
    background: var(--orange);
  }
  .appt {
    position: absolute; left: 36px; right: 36px; top: 96px;
  }
  .appt .line {
    height: 1px; background: var(--rule); margin-bottom: 24px;
  }
  .appt .field {
    display: flex; align-items: flex-end; gap: 8px;
    font-size: 15px; color: var(--ink); margin-bottom: 22px;
  }
  .appt .field .fill { flex: 1; border-bottom: 1px solid var(--rule); height: 14px; }
  .appt .field .suffix { font-size: 12px; }
  .appt .row { display: flex; gap: 24px; }
  .appt .row .field { flex: 1; }
  .locations {
    position: absolute; left: 36px; right: 36px; bottom: 34px;
    display: grid; grid-template-columns: 1fr 1fr; row-gap: 8px;
    list-style: none; font-size: 14px;
  }
  .locations li { display: flex; align-items: center; gap: 8px; }
  .locations li::before {
    content: ""; width: 11px; height: 11px; border: 1.5px solid var(--blue);
  }

  /* front side */
  .brand-large {
    position: absolute; left: 0; right: 0; top: 52px; text-align: center;
  }
  .brand-large .name {
    font-family: "Marcellus", Georgia, serif;
    font-size: 58px; color: var(--navy); line-height: 1;
  }
  .brand-large .tag {
    font-family: "Marcellus", Georgia, serif;
    font-size: 26px; color: var(--green); margin-top: 2px;
  }
  .person { position: absolute; left: 0; right: 0; top: 172px; text-align: center; }
  .person .pname { font-weight: 700; font-size: 20px; color: var(--navy); }
  .person .role { font-weight: 700; font-size: 15px; color: var(--green); margin-top: 2px; }
  .rule {
    position: absolute; left: 40px; right: 40px; height: 1.5px;
    background: linear-gradient(90deg, var(--navy), var(--blue));
  }
  .rule.top { top: 230px; }
  .rule.bottom { top: 296px; }
  .contact {
    position: absolute; left: 40px; right: 40px; top: 242px;
    text-align: center; font-size: 14px; line-height: 1.6; color: var(--ink);
  }
  .contact b { color: var(--label-red); font-weight: 700; }
  .contact span { margin: 0 6px; }
</style>
</head>
<body>
  <section class="card card-back" aria-label="Appointment side">
    <div class="brand-small">
      <span class="dot"></span>
      <div class="name">Brightfield<small>Nutrition &amp; Dietetics</small></div>
    </div>
    <div class="cert-badge" role="img" aria-label="Certified Clinical Nutritionist badge"></div>
    <div class="appt">
      <div class="line"></div>
      <div class="row">
        <div class="field">Date :<span class="fill"></span></div>
        <div class="field">Time :<span class="fill"></span><span class="suffix">AM/PM</span></div>
      </div>
    </div>
    <ul class="locations">
      <li>Pinebrook Medical Centre</li>
      <li>Ashcombe Doctors Surgery</li>
      <li>North Corrin Health</li>
      <li>Hollis Medical</li>
    </ul>
  </section>

  <section class="card card-front" aria-label="Contact side">
    <div class="brand-large">
      <div class="name">Brightfield</div>
      <div class="tag">Nutrition &amp; Dietetics</div>
    </div>
    <div class="person">
      <div class="pname">Marcus Kellaway</div>
      <div class="role">Nutritionist &amp; Chef</div>
    </div>
    <div class="rule top"></div>
    <div class="contact">
      <span><b>P:</b> 0427 561 903</span><span><b>F:</b> 6457 2183</span><span><b>E:</b> marcus.k.diet@fernmail.com</span><br>
      <span><b>W:</b> www.brightfieldnutrition.com.au</span>
    </div>
    <div class="rule bottom"></div>
  </section>
</body>
</html>
```